Business Card Design

Online clothing womens clothing store, I sell my clothing online and at the markets.

i would like the attached picture on the front of the card and the contact information on the back.

Industry/Entity Type

Business

Contact Information for Business Card

Marlow Thread
Karen Whitfield
(Instagram symbol) _marlow_thread_
(Facebook symbol) www.fakebookexample.com/marlowthreadau/

W : www.marlowthread.example.au
E : info@marlowthread.example.au
P : 0498716204

```html
<!DOCTYPE html>
<html lang="en">
<head>
<meta charset="utf-8">
<title>Marlow Thread — Business Card</title>
<link rel="stylesheet" href="https://fonts.googleapis.com/css2?family=Open+Sans:wght@400;600&display=swap">
<style>
  :root {
    --page-bg: #ecebe8;
    --card-white: #ffffff;
    --ink: #111111;
    --ink-soft: #333333;
    --photo-light: #dfe6e8;
    --photo-mid: #a9b6bb;
    --photo-dark: #3d4248;
    --brand-text: #f4f4f2;
  }
  * { margin: 0; padding: 0; box-sizing: border-box; }
  html, body {
    width: 1200px; height: 900px; overflow: hidden;
    background: var(--page-bg);
    font-family: "Open Sans", Arial, sans-serif;
  }
  .canvas { position: relative; width: 1200px; height: 900px; }

  .card {
    position: absolute;
    box-shadow: 0 6px 22px rgba(0,0,0,0.14);
    overflow: hidden;
  }

  /* Back: contact details */
  .card-back {
    left: 238px; top: 62px; width: 555px; height: 342px;
    background: var(--card-white);
    color: var(--ink-soft);
  }
  .holder-name {
    position: absolute; right: 38px; top: 66px;
    font-size: 29px; font-weight: 600; color: var(--ink);
    letter-spacing: -0.2px;
  }
  .contact-list {
    position: absolute; left: 46px; list-style: none;
    font-size: 14.5px; line-height: 20px;
  }
  .contact-list.primary { top: 173px; }
  .contact-list.social { top: 265px; }
  .contact-list li { display: flex; align-items: center; gap: 9px; }
  .contact-list svg { width: 12px; height: 12px; flex: none; fill: var(--ink); }

  /* Front: photo and brand name */
  .card-front {
    left: 457px; top: 518px; width: 561px; height: 344px;
  }
  .front-photo {
    position: absolute; inset: 0;
    background:
      radial-gradient(ellipse at 72% 45%, var(--photo-dark) 0%, #5e666c 30%, transparent 62%),
      linear-gradient(100deg, var(--photo-light) 0%, #cfd9dc 40%, var(--photo-mid) 70%, #6f777c 100%);
  }
  .brand-name {
    position: absolute; left: 32px; bottom: 20px;
    font-size: 54px; font-weight: 600; line-height: 1;
    letter-spacing: 2px; text-transform: uppercase;
    color: var(--brand-text); white-space: nowrap;
  }
</style>
</head>
<body>
<main class="canvas">

  <section class="card card-back" aria-label="Business card back">
    <h1 class="holder-name">Karen Whitfield</h1>
    <ul class="contact-list primary">
      <li>
        <svg viewBox="0 0 12 12" aria-hidden="true"><path d="M1 4c0-1.5 2-3 5-3s5 1.5 5 3v1H8.5V3.8h-5V5H1zM3 6h6l1.5 4.5h-9z"/></svg>
        0498716204
      </li>
      <li>
        <svg viewBox="0 0 12 12" aria-hidden="true"><path d="M1 3h10v6.5H1z M1.5 3.4 6 6.8l4.5-3.4" stroke="#fff" stroke-width="0.9"/></svg>
        info@marlowthread.example.au
      </li>
      <li>
        <svg viewBox="0 0 12 12" aria-hidden="true"><path d="M5 7 7 5M4.4 5.3 3 6.7a1.8 1.8 0 0 0 2.5 2.5l1.4-1.4M7.6 6.7 9 5.3A1.8 1.8 0 0 0 6.5 2.8L5.1 4.2" fill="none" stroke="#111" stroke-width="1.3" stroke-linecap="round"/></svg>
        www.marlowthread.example.au
      </li>
    </ul>
    <ul class="contact-list social">
      <li>
        <svg viewBox="0 0 12 12" aria-hidden="true"><rect x="1" y="1" width="10" height="10" rx="1.5"/></svg>
        _marlow_thread_
      </li>
      <li>
        <svg viewBox="0 0 12 12" aria-hidden="true"><rect x="1" y="1" width="10" height="10" rx="1.5"/></svg>
        www.fakebookexample.com/marlowthreadau/
      </li>
    </ul>
  </section>

  <section class="card card-front" aria-label="Business card front">
    <div class="front-photo" role="img" aria-label="Misty pale blue-grey photograph with a dark grey subject on the right side"></div>
    <p class="brand-name">Marlow Thread</p>
  </section>

</main>
</body>
</html>
```